Non fiction book cover. The book advises how to get a new job.

The book size will be 20cm high by 13cm wide and I need a front cover which can wrap around to the back. This book has a serious message, but I've tried to make it quite light to read and accessible. So I don't want a cover that is too dour or serious and not frivolous either. At the end of the project, I will need a high resolution 3D image of the book, included as part of the package.<br/>The Title of the book is:- "Past Sixty? Hunting for your final post?<br/>by Gareth Millbrook-Ashdown".<br/>I am thinking of a light yellow background, with a striking image to attract attention. The image and words should be clear and sharp.<br/>Here is the, BACK COVER wording.<br/>"This book tells you clearly and simply the steps that you need to take, to get a job, once you’re over 50.<br/>It advises you on the techniques to use to write a killer CV.<br/>It explains how to ensure that your CV attention.<br/>It shows the best way to approach your local job agency.<br/>It demonstrates the best way to use your network.<br/><br/>This book, written by someone with 30 years’ experience in the recruitment industry, gives you ALL the answers.<br/>Whether you are a top executive or someone after some local part time work, then this book is for you. <br/>With the help of this book you will secure your next position.<br/>

Target Market(s)

UK, over 50s, male and female.

Font styles to use
Serif

Colors
fbee3e

Requirements
Must have
• A clear uncluttered cover.
Should not have
• Fussy and over complicated

```html
<!DOCTYPE html>
<html lang="en">
<head>
<meta charset="utf-8">
<title>Past Sixty? Hunting for your final post? — Book Cover Wrap</title>
<link href="https://fonts.googleapis.com/css2?family=Bebas+Neue&family=Cinzel:wght@700&family=Cormorant+Garamond:wght@400&family=Crimson+Text:ital,wght@0,400;1,600&display=swap" rel="stylesheet">
<style>
  :root {
    --yellow: #f9ec3f;
    --teal: #3fbfa9;
    --red: #d7303f;
    --pink: #e9707a;
    --ink: #1d1d1b;
    --stage: #f3f3f3;
  }
  * { margin: 0; padding: 0; box-sizing: border-box; }
  html, body {
    width: 1200px; height: 800px; overflow: hidden;
    background: var(--stage);
  }
  body { position: relative; }
  .cover-wrap {
    position: absolute; left: 124px; top: 50px;
    width: 952px; height: 700px;
    background: var(--yellow);
    box-shadow: 0 4px 18px rgba(0,0,0,.12);
    display: flex;
    overflow: hidden;
  }
  .panel { position: relative; height: 100%; overflow: hidden; }
  .back-cover { width: 443px; }
  .spine { width: 60px; }
  .front-cover { width: 449px; }

  .base-band {
    position: absolute; left: 0; right: 0; bottom: 0;
    height: 53px; background: var(--teal);
  }
  .kicker {
    font-family: "Cormorant Garamond", serif;
    color: var(--teal); line-height: 1; text-align: center;
  }
  .headline {
    font-family: "Bebas Neue", sans-serif;
    color: var(--red); line-height: .9; text-align: center;
    text-shadow: 0 0 12px rgba(255,255,255,.75);
  }
  .author {
    font-family: "Cinzel", serif; font-weight: 700; color: var(--ink);
    letter-spacing: .02em; white-space: nowrap;
  }

  /* Back cover */
  .back-cover .kicker { margin-top: 40px; font-size: 26px; }
  .back-cover .headline { font-size: 36px; margin-top: 2px; }
  .blurb {
    margin: 22px 42px 0 42px;
    font-family: "Crimson Text", serif; font-size: 13.5px; line-height: 1.3;
    color: var(--ink);
  }
  .blurb p + p { margin-top: 14px; }
  .blurb ul { margin: 16px 0 18px 22px; list-style: none; }
  .blurb li {
    position: relative; font-style: italic; font-weight: 600; font-size: 12.5px;
    margin-bottom: 12px; padding-left: 14px;
  }
  .blurb li::before {
    content: ""; position: absolute; left: -4px; top: 6px;
    width: 6px; height: 6px; border-radius: 50%; background: var(--ink);
  }
  .back-art {
    position: absolute; left: 53px; top: 470px; width: 260px; height: 177px;
    background: linear-gradient(180deg, rgba(63,191,169,0) 0%, rgba(63,191,169,.55) 60%, var(--teal) 100%);
  }

  /* Spine */
  .spine-title {
    position: absolute; left: 50%; top: 30px; transform: translateX(-50%);
    writing-mode: vertical-rl; white-space: nowrap;
    display: flex; align-items: center; gap: 8px;
  }
  .spine-title .kicker { font-size: 16px; }
  .spine-title .headline { font-size: 24px; text-shadow: none; }
  .spine-author {
    position: absolute; left: 50%; bottom: 68px; transform: translateX(-50%);
    writing-mode: vertical-rl; font-size: 11px;
  }

  /* Front cover */
  .front-cover .kicker { margin-top: 36px; font-size: 58px; }
  .front-cover .headline { font-size: 84px; margin-top: 4px; }
  .front-art {
    position: absolute; left: 20px; right: 20px; top: 400px; height: 248px;
    background: linear-gradient(180deg, rgba(63,191,169,0) 0%, rgba(233,112,122,.45) 55%, var(--teal) 100%);
  }
  .front-cover .base-band {
    display: flex; align-items: center; justify-content: center;
  }
  .front-cover .author { font-size: 22px; }
</style>
</head>
<body>
  <main class="cover-wrap">
    <section class="panel back-cover">
      <p class="kicker">PAST SIXTY?</p>
      <h2 class="headline">HUNTING FOR YOUR FINAL POST?</h2>
      <div class="blurb">
        <p>This book tells you the steps that you need to take, to get a job once you’re over 50.</p>
        <ul>
          <li>It gives you all the tips you need to write a killer CV.</li>
          <li>It explains how ensure that your CV gets attention.</li>
          <li>It advises you how to approach your local job agency.</li>
          <li>It guides you through the steps you need to take to make effective use of your network.</li>
        </ul>
        <p>This book, written by someone with 30 years’ experience in the recruitment industry, gives you all the answers. Whether you are a top executive or someone after some local part time work, then this book is for you.</p>
        <p>It will help you to secure your next position.</p>
      </div>
      <div class="back-art" role="img" aria-label="Small illustration of a climber sitting on a teal and pink geometric mountain peak with clouds"></div>
      <div class="base-band"></div>
    </section>

    <section class="panel spine">
      <div class="spine-title">
        <span class="kicker">PAST SIXTY?</span>
        <span class="headline">HUNTING FOR YOUR FINAL POST?</span>
      </div>
      <span class="author spine-author">GARETH MILLBROOK-ASHDOWN</span>
      <div class="base-band"></div>
    </section>

    <section class="panel front-cover">
      <p class="kicker">PAST SIXTY?</p>
      <h1 class="headline">HUNTING FOR<br>YOUR FINAL<br>POST?</h1>
      <div class="front-art" role="img" aria-label="Illustration of a job seeker with a backpack sitting atop a geometric teal and pink mountain, with a thought cloud and pink and teal clouds"></div>
      <div class="base-band"><span class="author">GARETH MILLBROOK-ASHDOWN</span></div>
    </section>
  </main>
</body>
</html>
```